Building company buisness cards

We are looking for a sharp modern new look for our business cards.
We are a New Zealand based company that specialises in house and land packages.
We have attached a photo of the current logo and would like to see if it can be improved somehow if needed.
We are open to any colours but we have chosen green at this stage.
Feel free to change the font and make the logo smarter looking.
Play with the colours and see what looks best.

We want a card that looks so good know one will want to throw it away!

Target Market(s)

Home buyers

Industry/Entity Type

Building

Contact Information for Business Card

Derek Tolvane
0217394062
dtolvane@quillmarkhomesteads.co.nz
quillmarkhomesteads.co.nz

Font styles to use
Serif
Sans Serif

Colors

Designer to choose colors to be used in the design.

Requirements
Must have
• Logo and company name on one side, details on the other side
Nice to have
• Color codes for the original green are HEX #4a8028, RGB(74,128,40), CMYK(42,0,69,50)
• Round corners, Raised and/or spot UV

```html
<!DOCTYPE html>
<html lang="en">
<head>
<meta charset="utf-8">
<title>Quillmark Homesteads – Business Cards</title>
<link rel="stylesheet" href="https://fonts.googleapis.com/css2?family=Lato:wght@400;700&display=swap">
<style>
  :root {
    --stage: #262626;
    --card-dark: #161616;
    --brand-green: #4a8028;
    --text-light: #ffffff;
    --text-muted: #d9d9d9;
    --rule: rgba(255,255,255,0.45);
  }
  * { box-sizing: border-box; margin: 0; padding: 0; }
  html, body {
    width: 1200px; height: 900px; overflow: hidden;
    background: var(--stage);
    font-family: "Lato", Arial, sans-serif;
  }
  .sheet { position: relative; width: 1200px; height: 900px; }
  .card {
    position: absolute; left: 300px;
    width: 600px; height: 343px;
    border-radius: 26px;
    overflow: hidden;
  }
  .card--back { top: 84px; background: var(--card-dark); }
  .card--front { top: 473px; background: var(--brand-green); }

  .brand {
    position: absolute;
    display: flex; align-items: center; gap: 14px;
  }
  .brand-mark { flex: none; border-radius: 50%; }
  .brand-name {
    font-family: "Lato", Arial, sans-serif;
    font-weight: 700;
    line-height: 1;
    white-space: nowrap;
  }

  .card--back .brand {
    left: 0; right: 0; top: 118px; justify-content: center;
  }
  .card--back .brand-mark { width: 54px; height: 54px; background: var(--brand-green); }
  .card--back .brand-name { font-size: 34px; color: var(--brand-green); }
  .card--back .web {
    position: absolute; left: 0; right: 0; bottom: 56px;
    text-align: center; font-size: 14px; color: var(--text-muted);
    letter-spacing: 0.2px;
  }

  .card--front .brand { right: 44px; top: 62px; }
  .card--front .brand-mark { width: 36px; height: 36px; background: var(--text-light); }
  .card--front .brand-name { font-size: 32px; color: var(--text-light); }
  .card--front .brand-rule {
    position: absolute; right: 130px; top: 120px;
    width: 110px; height: 1px; background: var(--rule);
  }

  .contact {
    position: absolute; left: 40px; bottom: 36px;
    color: var(--text-light);
  }
  .contact .person {
    font-weight: 700; font-size: 19px; text-transform: uppercase;
    margin-bottom: 12px; letter-spacing: 0.2px;
  }
  .contact ul { list-style: none; }
  .contact li {
    display: flex; align-items: center; gap: 8px;
    font-size: 16px; line-height: 22px;
  }
  .contact svg { width: 13px; height: 13px; flex: none; fill: var(--text-light); }
</style>
</head>
<body>
<main class="sheet">
  <section class="card card--back" aria-label="Card back">
    <div class="brand">
      <span class="brand-mark" aria-hidden="true"></span>
      <p class="brand-name">Quillmark Homesteads</p>
    </div>
    <p class="web">www.quillmarkhomesteads.co.nz</p>
  </section>

  <section class="card card--front" aria-label="Card front">
    <div class="brand">
      <span class="brand-mark" aria-hidden="true"></span>
      <p class="brand-name">Quillmark Homesteads</p>
    </div>
    <div class="brand-rule"></div>

    <div class="contact">
      <p class="person">Derek Tolvane</p>
      <ul>
        <li>
          <svg viewBox="0 0 16 16" aria-hidden="true"><path d="M2 5c0-2 2-3 6-3s6 1 6 3v1h-3V5H5v1H2zM4 7h8l2 6H2z"/></svg>
          0217394062
        </li>
        <li>
          <svg viewBox="0 0 16 16" aria-hidden="true"><path d="M1 3h14v10H1zM2.5 4.5v.4L8 9l5.5-4.1v-.4z"/></svg>
          dtolvane@quillmarkhomesteads.co.nz
        </li>
        <li>
          <svg viewBox="0 0 16 16" aria-hidden="true"><path d="M8 1a7 7 0 1 0 0 14A7 7 0 0 0 8 1zm0 1.6c1 1.2 1.6 3.2 1.6 5.4S9 12.2 8 13.4C7 12.2 6.4 10.2 6.4 8S7 3.8 8 2.6zM2.7 7.3h2.4v1.4H2.7zm8.2 0h2.4v1.4h-2.4z"/></svg>
          www.quillmarkhomesteads.co.nz
        </li>
      </ul>
    </div>
  </section>
</main>
</body>
</html>
```